Coastline Premier Retreats Business Card Design

Design a business card for Coastline Premier Retreats. Look at the website for colors and reference. Card should have logo, name, title, office number, mobile number, email, URL and a tagline like, "Luxury Hotel & Resort Email Marketing" (This might change).

https://www.coastlinepremierretreats.example

The rest I will leave up to your imagination.

Contact Information for Business Card

Logo, name, title, office number, mobile number, email, URL and a tagline like, "Luxury Hotel & Resort Email Marketing" (This might change).

```html
<!DOCTYPE html>
<html lang="en">
<head>
<meta charset="utf-8">
<title>Coastline Premier Retreats – Business Card</title>
<link rel="stylesheet" href="https://fonts.googleapis.com/css2?family=Archivo+Black&family=Ubuntu:wght@400;500&display=swap">
<style>
  :root {
    --backdrop: #2d2d2d;
    --card: #000000;
    --accent: #ff6f00;
    --ink: #ffffff;
    --card-w: 560px;
    --card-h: 320px;
  }
  * { box-sizing: border-box; margin: 0; padding: 0; }
  html, body {
    width: 1200px;
    height: 1015px;
    overflow: hidden;
    background: var(--backdrop);
  }
  .canvas {
    position: relative;
    width: 1200px;
    height: 1015px;
  }
  .card {
    position: absolute;
    width: var(--card-w);
    height: var(--card-h);
    background: var(--card);
    box-shadow: 0 14px 30px rgba(0,0,0,0.55);
    overflow: hidden;
  }
  .card--front { left: 110px; top: 130px; }
  .card--back  { left: 530px; top: 545px; }

  .card__band {
    position: absolute;
    left: 0; right: 0; bottom: 0;
    height: 9px;
    background: var(--accent);
  }

  .wordmark {
    position: absolute;
    display: flex;
    align-items: center;
    gap: 12px;
    font-family: "Archivo Black", sans-serif;
    color: var(--ink);
    text-transform: uppercase;
    line-height: 1.05;
  }
  .wordmark__square {
    width: 16px; height: 16px;
    background: var(--accent);
    flex: none;
  }
  .card--front .wordmark {
    left: 0; right: 0; top: 92px;
    justify-content: center;
    font-size: 25px;
    letter-spacing: 1px;
  }
  .tagline {
    position: absolute;
    left: 0; right: 0; top: 212px;
    text-align: center;
    font-family: "Archivo Black", sans-serif;
    font-size: 13px;
    letter-spacing: 1.2px;
    color: var(--ink);
    text-transform: uppercase;
  }

  .card--back .wordmark {
    right: 34px; top: 70px;
    font-size: 17px;
    letter-spacing: 0.8px;
    width: 230px;
  }
  .person {
    position: absolute;
    left: 36px; top: 56px;
  }
  .person__name {
    font-family: "Archivo Black", sans-serif;
    font-size: 19px;
    letter-spacing: 1.2px;
    color: var(--accent);
    text-transform: uppercase;
  }
  .person__title {
    font-family: "Ubuntu", sans-serif;
    font-size: 15px;
    color: var(--ink);
    margin-top: 2px;
  }
  .contacts {
    position: absolute;
    left: 36px; bottom: 36px;
    list-style: none;
    font-family: "Ubuntu", sans-serif;
    font-size: 14.5px;
    color: var(--ink);
  }
  .contacts li {
    display: flex;
    align-items: center;
    gap: 10px;
    margin-top: 5px;
  }
  .contacts svg {
    width: 15px; height: 15px;
    flex: none;
    fill: none;
    stroke: var(--accent);
    stroke-width: 2;
    stroke-linecap: round;
    stroke-linejoin: round;
  }
</style>
</head>
<body>
<main class="canvas">

  <section class="card card--front" aria-label="Card front">
    <div class="wordmark">
      <span class="wordmark__square"></span>
      <span>Coastline Premier Retreats</span>
    </div>
    <p class="tagline">Luxury Hotel &amp; Resort Email Marketing</p>
    <div class="card__band"></div>
  </section>

  <section class="card card--back" aria-label="Card back">
    <div class="person">
      <h1 class="person__name">Daniel Hartley</h1>
      <p class="person__title">Managing Director</p>
    </div>

    <div class="wordmark">
      <span class="wordmark__square"></span>
      <span>Coastline Premier Retreats</span>
    </div>

    <ul class="contacts">
      <li>
        <svg viewBox="0 0 24 24" aria-hidden="true"><path d="M5 3h4l2 5-2.5 1.5a11 11 0 0 0 6 6L16 13l5 2v4a2 2 0 0 1-2 2A16 16 0 0 1 3 5a2 2 0 0 1 2-2z"/></svg>
        <span>044-555 010 200</span>
      </li>
      <li>
        <svg viewBox="0 0 24 24" aria-hidden="true"><rect x="6" y="2" width="12" height="20" rx="2"/><path d="M11 18h2"/></svg>
        <span>044-555 010 300</span>
      </li>
      <li>
        <svg viewBox="0 0 24 24" aria-hidden="true"><rect x="2" y="5" width="20" height="14" rx="1"/><path d="M2 6l10 7 10-7"/></svg>
        <span>info@coastlinepremierretreats.example</span>
      </li>
      <li>
        <svg viewBox="0 0 24 24" aria-hidden="true"><circle cx="12" cy="12" r="10"/><path d="M2 12h20M12 2a15 15 0 0 1 0 20M12 2a15 15 0 0 0 0 20"/></svg>
        <span>www.coastlinepremierretreats.example</span>
      </li>
    </ul>
    <div class="card__band"></div>
  </section>

</main>
</body>
</html>
```